SaaS Early tech startup business card design

Unique design for experience ecommerce platform company. the business cards will be used by executive members. conformance with color code is required.

```html
<!DOCTYPE html>
<html lang="en">
<head>
<meta charset="utf-8">
<title>Korvi — Business Card</title>
<link href="https://fonts.googleapis.com/css2?family=Montserrat:wght@500;700&family=Arimo:wght@400&display=swap" rel="stylesheet">
<style>
  :root {
    --stage: #2e2e2e;
    --paper: #ffffff;
    --teal: #12a596;
    --teal-deep: #0f9495;
    --blue: #0d6792;
    --ink: #2b2b2b;
    --rule: #e3e3e3;
  }
  * { margin: 0; padding: 0; box-sizing: border-box; }
  html, body {
    width: 1200px; height: 866px; overflow: hidden;
    background: var(--stage);
  }
  .stage {
    position: relative; width: 1200px; height: 866px;
  }
  .card {
    position: absolute; top: 285px;
    width: 520px; height: 297px;
    box-shadow: 0 8px 22px rgba(0,0,0,.45);
    overflow: hidden;
  }
  .card--front { left: 60px; background: var(--paper); }
  .card--back { left: 620px; }

  .contact {
    position: absolute; left: 34px; top: 46px;
    font-family: "Arimo", sans-serif; color: var(--ink);
  }
  .contact__name {
    font-family: "Montserrat", sans-serif; font-weight: 500;
    font-size: 19px; letter-spacing: 0.5px; text-transform: uppercase;
    color: var(--teal-deep); line-height: 1.1;
  }
  .contact__title { font-size: 13px; margin-top: 3px; margin-bottom: 10px; }
  .contact__list { list-style: none; font-size: 12px; line-height: 18px; }
  .contact__list li { display: flex; align-items: center; gap: 6px; }
  .contact__list svg { width: 11px; height: 11px; flex: none; }

  .wordmark {
    font-family: "Montserrat", sans-serif; font-weight: 700;
    letter-spacing: -1px; line-height: 1;
  }
  .card--front .wordmark {
    position: absolute; right: 40px; top: 64px;
    font-size: 66px; color: var(--teal);
  }

  .divider {
    position: absolute; left: 34px; right: 34px; top: 208px;
    height: 1px; background: var(--rule);
  }
  .address {
    position: absolute; right: 40px; bottom: 30px; text-align: right;
    font-family: "Arimo", sans-serif; font-size: 13px; line-height: 18px;
    color: var(--ink);
  }

  .card__pattern {
    position: absolute; inset: 0;
    background: linear-gradient(135deg, var(--teal) 0%, #119a98 45%, var(--blue) 100%);
  }
  .card--back .wordmark {
    position: absolute; left: 0; right: 0; top: 50%;
    transform: translateY(-50%); text-align: center;
    font-size: 78px; color: #ffffff;
  }
</style>
</head>
<body>
<main class="stage">
  <section class="card card--front">
    <div class="contact">
      <h1 class="contact__name">Daniel Reyes</h1>
      <p class="contact__title">Managing Director</p>
      <ul class="contact__list">
        <li>
          <svg viewBox="0 0 12 12" aria-hidden="true"><path d="M3 1.5 L4.6 3.6 L3.7 4.6 Q4.8 7 7.4 8.3 L8.4 7.4 L10.5 9 L9.3 10.6 Q4.5 10 1.5 3.2 Z" fill="var(--teal)"/></svg>
          055-842 317 620
        </li>
        <li>
          <svg viewBox="0 0 12 12" aria-hidden="true"><rect x="1" y="2.5" width="10" height="7" fill="var(--teal)"/><path d="M1 2.5 L6 6.5 L11 2.5" stroke="#fff" stroke-width="1" fill="none"/></svg>
          hello@korvi.io
        </li>
        <li>
          <svg viewBox="0 0 12 12" aria-hidden="true"><circle cx="6" cy="6" r="4.8" fill="none" stroke="var(--teal)" stroke-width="1.2"/><ellipse cx="6" cy="6" rx="2" ry="4.8" fill="none" stroke="var(--teal)" stroke-width="1"/><path d="M1.2 6 H10.8" stroke="var(--teal)" stroke-width="1"/></svg>
          www.korvi.io
        </li>
      </ul>
    </div>
    <div class="wordmark">Korvi</div>
    <div class="divider"></div>
    <address class="address">18, Harbor Lane Suite 400<br>30917, Eastland</address>
  </section>

  <section class="card card--back">
    <div class="card__pattern" role="img" aria-label="Checkered teal to blue gradient pattern"></div>
    <div class="wordmark">Korvi</div>
  </section>
</main>
</body>
</html>
```